Orvane Group Business Card

Building Management company based in Sydney, Australia. We provide onsite management for commercial and residential buildings.
I would like a sophisticated minimalist design that indicates that we provide a high-end service. I would like a silver or metal look background or something similar.
The business card should have:
Name
Title
email
Office Phone
Mobile
Address
Website
The services that we provide should be prominent:
Building Management - Concierge - Caretaking - Cleaning

```html
<!DOCTYPE html>
<html lang="en">
<head>
<meta charset="utf-8">
<title>Orvane Group Business Card</title>
<link rel="stylesheet" href="https://fonts.googleapis.com/css2?family=Open+Sans:wght@400;600;700;800&display=swap">
<style>
  :root {
    --backdrop: #2b2b2d;
    --metal-light: #f2f2f2;
    --metal-mid: #d6d6d8;
    --metal-dark: #b9b9bc;
    --brand-blue: #1b64ad;
    --ink: #1b1b1b;
    --ink-soft: #2e2e2e;
  }
  * { box-sizing: border-box; margin: 0; padding: 0; }
  html, body {
    width: 1200px; height: 852px; overflow: hidden;
    background: var(--backdrop);
    font-family: "Open Sans", Arial, sans-serif;
  }
  .stage { position: relative; width: 1200px; height: 852px; }

  .card {
    position: absolute;
    border-radius: 22px;
    overflow: hidden;
    box-shadow: 0 14px 30px rgba(0,0,0,.45);
    background:
      repeating-linear-gradient(178deg, rgba(255,255,255,.35) 0 1px, rgba(0,0,0,.04) 1px 3px, rgba(255,255,255,.15) 3px 4px),
      linear-gradient(120deg, var(--metal-mid) 0%, var(--metal-light) 35%, var(--metal-dark) 60%, var(--metal-light) 85%, var(--metal-mid) 100%);
  }

  .wordmark {
    display: flex; align-items: center; gap: 12px;
    font-weight: 800; color: var(--ink); letter-spacing: 1px; white-space: nowrap;
  }
  .wordmark__square { width: 14px; height: 14px; background: var(--brand-blue); flex: none; }

  /* Front */
  .card--front { left: 130px; top: 90px; width: 540px; height: 310px; }
  .card--front .wordmark {
    position: absolute; left: 0; right: 0; top: 96px;
    justify-content: center; font-size: 44px;
  }
  .front-rule { position: absolute; height: 3px; background: var(--brand-blue); }
  .front-rule--top { left: 368px; top: 84px; width: 70px; }
  .front-rule--bottom { left: 110px; top: 212px; width: 70px; }
  .website {
    position: absolute; left: 0; right: 0; top: 180px;
    text-align: center; font-size: 15px; letter-spacing: 3px; color: var(--ink-soft);
  }
  .services {
    position: absolute; left: 0; right: 0; top: 236px;
    display: flex; justify-content: center; gap: 10px; list-style: none;
    font-size: 11px; font-weight: 700; letter-spacing: 1.5px;
    text-transform: uppercase; color: var(--brand-blue); white-space: nowrap;
  }
  .services li + li::before { content: "•"; margin-right: 10px; color: var(--ink-soft); }

  /* Back */
  .card--back { left: 520px; top: 440px; width: 540px; height: 310px; }
  .card__shapes { position: absolute; inset: 0; }
  .card--back .wordmark { position: absolute; left: 40px; top: 120px; font-size: 30px; }
  .person { position: absolute; right: 150px; top: 48px; text-align: right; }
  .person__name { font-size: 19px; font-weight: 700; color: var(--brand-blue); }
  .person__title { font-size: 11px; color: var(--ink-soft); }
  .contacts { position: absolute; left: 40px; top: 206px; list-style: none; }
  .contacts li {
    display: flex; align-items: center; gap: 10px;
    font-size: 13px; line-height: 17px; color: var(--ink-soft);
  }
  .contacts svg { width: 13px; height: 13px; flex: none; fill: var(--brand-blue); }
  .contacts .address { align-items: flex-start; }
</style>
</head>
<body>
<main class="stage">

  <section class="card card--front" aria-label="Card front">
    <span class="front-rule front-rule--top"></span>
    <div class="wordmark"><span class="wordmark__square"></span>ORVANE GROUP</div>
    <p class="website">www.orvanegroup.com.au</p>
    <span class="front-rule front-rule--bottom"></span>
    <ul class="services">
      <li>Building Management</li>
      <li>Concierge</li>
      <li>Caretaking</li>
      <li>Cleaning</li>
    </ul>
  </section>

  <section class="card card--back" aria-label="Card back">
    <svg class="card__shapes" viewBox="0 0 540 310" preserveAspectRatio="none" aria-hidden="true">
      <polygon points="0,100 330,0 430,0 0,190" fill="#ffffff"/>
      <polygon points="0,190 430,0 445,0 0,200" fill="#e4e4e6"/>
      <polygon points="405,0 540,0 540,300 470,300 445,40" fill="#1b64ad"/>
    </svg>

    <div class="person">
      <p class="person__name">Your Long Name</p>
      <p class="person__title">Managing Director</p>
    </div>

    <div class="wordmark"><span class="wordmark__square"></span>ORVANE GROUP</div>

    <ul class="contacts">
      <li>
        <svg viewBox="0 0 16 16"><path d="M3 1h3l1.5 4-2 1.2a9 9 0 0 0 4.3 4.3L11 8.5 15 10v3a2 2 0 0 1-2 2A12 12 0 0 1 1 3a2 2 0 0 1 2-2z"/></svg>
        00.00.00.0000
      </li>
      <li>
        <svg viewBox="0 0 16 16"><path d="M4 0h8a1 1 0 0 1 1 1v14a1 1 0 0 1-1 1H4a1 1 0 0 1-1-1V1a1 1 0 0 1 1-1zm1 2v10h6V2zm3 11a1 1 0 1 0 0 2 1 1 0 0 0 0-2z"/></svg>
        00.00.00.0000
      </li>
      <li>
        <svg viewBox="0 0 16 16"><path d="M0 3h16v10H0zm1.5 1.5L8 9l6.5-4.5V4h-13z"/></svg>
        yourname@yourwebsite.com
      </li>
      <li class="address">
        <svg viewBox="0 0 16 16"><path d="M8 0a5.5 5.5 0 0 1 5.5 5.5C13.5 10 8 16 8 16S2.5 10 2.5 5.5A5.5 5.5 0 0 1 8 0zm0 3.5a2 2 0 1 0 0 4 2 2 0 0 0 0-4z"/></svg>
        <span>Your Commercial or office address<br>in just two line with pincode</span>
      </li>
    </ul>
  </section>

</main>
</body>
</html>
```